Letterhead and matching envelope design for a dental office

We need a new stationary design, letterhead and envelope #10, for a dental office in Denver area. We are called Bright Harbor Dental. We want a simple and minimalistic design but not a boring design. I wish to have one good point that makes it look professional. I have attached our logo. Feel free to use either one. I want the design for letterhead and envelope look like a "matching pair" but not look the same. The envelope doesn't have to be white and it will have an address window on bottom left.

Target Market(s)

everyone who visits dentist (adults)

Industry/Entity Type

Dental

Font styles to use
Other font styles liked:
• close to font on logo or something that matches well

Requirements
Must have
• professional
• simple, minimalistic
• unique point that stands out
Nice to have
• matching but not same design for letterhead and envelope
Should not have
• not look like all the other boring designs
• no flowery, distracting feats

```html
<!DOCTYPE html>
<html lang="en">
<head>
<meta charset="utf-8">
<title>Bright Harbor Dental – #10 Envelope</title>
<link href="https://fonts.googleapis.com/css2?family=Arimo:wght@400;700&display=swap" rel="stylesheet">
<style>
  :root {
    --brand-green: #3bb54a;
    --swoosh-mid: #a9d9ae;
    --swoosh-light: #d6eed8;
    --paper: #ffffff;
    --backdrop: #ecece8;
    --icon-disc: #e4f4e6;
  }
  html, body {
    margin: 0;
    width: 1200px;
    height: 800px;
    overflow: hidden;
    background: var(--backdrop);
  }
  .canvas {
    display: block;
    width: 1200px;
    height: 800px;
  }
  .envelope-flap { fill: var(--brand-green); }
  .envelope-body { fill: var(--paper); }
  .band-main { fill: var(--brand-green); }
  .band-white { fill: var(--paper); }
  .swoosh-mid { fill: var(--swoosh-mid); }
  .swoosh-light { fill: var(--swoosh-light); }
  .brand-name {
    font-family: "Arimo", Arial, sans-serif;
    font-weight: 700;
    text-anchor: middle;
    text-transform: uppercase;
  }
  .brand-name--front { fill: var(--brand-green); font-size: 22px; letter-spacing: 6px; }
  .brand-name--flap { fill: var(--paper); font-size: 13px; letter-spacing: 4px; }
  .brand-ring--front { fill: none; stroke: var(--brand-green); stroke-width: 2; }
  .brand-ring--flap { fill: none; stroke: var(--paper); stroke-width: 1.5; }
  .contact-text {
    font-family: "Arimo", Arial, sans-serif;
    font-size: 18px;
    fill: var(--paper);
  }
  .icon-disc { fill: var(--icon-disc); }
  .icon-glyph { fill: var(--brand-green); }
  .icon-line { fill: none; stroke: var(--brand-green); stroke-width: 1.4; }
</style>
</head>
<body>
<svg class="canvas" viewBox="0 0 1200 800" xmlns="http://www.w3.org/2000/svg" role="img" aria-label="Bright Harbor Dental #10 envelope">
  <!-- back flap -->
  <path class="envelope-flap" d="M125 277 C125 258 132 246 150 240 L580 116 Q600 110 620 116 L1050 240 C1068 246 1075 258 1075 277 Z"/>
  <g class="brand-mark brand-mark--flap">
    <circle class="brand-ring--flap" cx="600" cy="190" r="50"/>
    <text class="brand-name brand-name--flap" x="600" y="186">Bright Harbor</text>
    <text class="brand-name brand-name--flap" x="600" y="206">Dental</text>
  </g>

  <!-- envelope front -->
  <rect class="envelope-body" x="125" y="277" width="950" height="413"/>

  <g class="brand-mark brand-mark--front">
    <circle class="brand-ring--front" cx="600" cy="370" r="78"/>
    <text class="brand-name brand-name--front" x="600" y="364">Bright Harbor</text>
    <text class="brand-name brand-name--front" x="600" y="396">Dental</text>
  </g>

  <!-- wave band -->
  <path class="swoosh-light" d="M150 525 C380 470 640 490 820 540 C920 568 1000 570 1060 540 C990 590 900 600 800 585 C620 555 400 500 150 525 Z"/>
  <path class="swoosh-mid" d="M160 528 C400 490 620 520 800 570 C900 598 980 598 1065 538 C1000 610 890 625 790 605 C600 565 380 515 160 528 Z"/>
  <path class="band-main" d="M125 548 C340 505 560 540 760 600 C880 636 980 600 1075 535 L1075 690 L125 690 Z"/>

  <!-- contact details -->
  <g class="contact-item contact-item--phone">
    <circle class="icon-disc" cx="218" cy="582" r="10"/>
    <path class="icon-glyph" d="M213 576 l3 -1 2 4 -2 1.5 q1.5 3 4 4.5 l1.5 -2 4 2 -1 3 q-4 1 -8 -3.5 q-4.5 -4 -3.5 -8.5 z"/>
    <text class="contact-text" x="240" y="589">720-555-0142</text>
  </g>
  <g class="contact-item contact-item--email">
    <circle class="icon-disc" cx="218" cy="608" r="10"/>
    <rect class="icon-glyph" x="211.5" y="603.5" width="13" height="9" rx="1"/>
    <path d="M212 604.5 L218 609.5 L224 604.5" fill="none" stroke="#e4f4e6" stroke-width="1.2"/>
    <text class="contact-text" x="240" y="615">info@brightharbordental.com</text>
  </g>
  <g class="contact-item contact-item--web">
    <circle class="icon-disc" cx="218" cy="634" r="10"/>
    <circle class="icon-line" cx="218" cy="634" r="6.5"/>
    <ellipse class="icon-line" cx="218" cy="634" rx="3" ry="6.5"/>
    <path class="icon-line" d="M211.5 634 H224.5 M213 630 H223 M213 638 H223"/>
    <text class="contact-text" x="240" y="641">www.brightharbordental.com</text>
  </g>
  <g class="contact-item contact-item--address">
    <circle class="icon-disc" cx="218" cy="660" r="10"/>
    <path class="icon-glyph" d="M218 668 C214 663 213 660 213 657.5 A5 5 0 0 1 223 657.5 C223 660 222 663 218 668 Z"/>
    <circle cx="218" cy="657.5" r="1.8" fill="#e4f4e6"/>
    <text class="contact-text" x="240" y="667">4820 Linden Ridge Dr,Suite 210 Westminster, CO 80031</text>
  </g>
</svg>
</body>
</html>
```